Website Home Page for Women's Health Medical Office

Redesign existing homepage for website using existing logo. Current website location is www.meadowcrestwomens.com. Please give it a modern, streamlined, playful feel.

Please give it a feminine feel and make it bright and cheerful using logo colors.

Target Market(s)

Women between the ages of 25-45

Industry/Entity Type

Medical Office

Coding

Coded - Design and coding required

Number of Pages Required

1 page

Font styles to use
Sans Serif
Other font styles liked:
• SEGOI UI script for text and GIL SANS for bold (or their equivilent)

Colors
E54698
E96AAD
F1A4CE
F9D9EA
FCEFF6

Requirements
Must have
• Existing logo. Logo Colors. Feminine, cheerful, simple design. all relevant contact information
Nice to have
• clean lines and streamlined look
Should not have
• Cluttered

```html
<!DOCTYPE html>
<html lang="en">
<head>
<meta charset="utf-8">
<title>Meadowcrest OB/GYN – Personalized Medical Care For Women</title>
<link rel="stylesheet" href="https://fonts.googleapis.com/css2?family=Titillium+Web:wght@400;600;700&family=Montserrat:wght@400;500;600&family=Great+Vibes&display=swap">
<style>
:root{
  --pink:#E54698;
  --pink-mid:#E96AAD;
  --pink-soft:#F1A4CE;
  --pink-pale:#F9D9EA;
  --pink-mist:#FCEFF6;
  --ink:#1f1f1f;
  --text:#555;
  --white:#fff;
  --black:#000;
}
*{box-sizing:border-box;margin:0;padding:0}
html,body{width:1200px;height:3357px;overflow:hidden;background:var(--white)}
body{position:relative;font-family:'Montserrat',sans-serif;color:var(--ink)}
.abs{position:absolute}
.heading{font-family:'Titillium Web',sans-serif}
.btn{position:absolute;display:flex;align-items:center;justify-content:center;border-radius:30px;font-family:'Titillium Web',sans-serif;font-weight:700;font-size:15px;text-transform:uppercase;color:var(--white);background:var(--pink)}
.rule{position:absolute;height:6px;border-top:2px solid var(--pink-soft);border-bottom:2px solid var(--pink-soft)}

/* header */
.topbar{left:350px;top:0;width:850px;height:63px;background:var(--pink-mist);clip-path:polygon(0 0,100% 0,100% 100%,55px 100%)}
.logo{left:115px;top:48px;display:flex;align-items:center;gap:10px;font-family:'Titillium Web',sans-serif;font-weight:700;font-size:24px;color:var(--pink)}
.logo-dot{width:34px;height:34px;border-radius:50%;background:var(--pink)}
.contact-chip{top:18px;display:flex;align-items:center;gap:10px;font-size:13.5px;font-weight:600;color:var(--ink);white-space:nowrap}
.chip-icon{width:28px;height:28px;border-radius:50%;background:var(--pink);display:flex;align-items:center;justify-content:center}
.search{left:811px;top:15px;width:275px;height:36px;border:1px solid #ddd;background:var(--white);font-size:13px;color:#999;padding:9px 14px}
.nav{top:107px;font-size:16px;font-weight:500;color:#333}

/* hero */
.hero{left:0;top:166px;width:1200px;height:643px;background:linear-gradient(90deg,#EE5FA8 0%,#F07CB8 30%,#e9c9cf 58%,#c9b4ad 100%)}
.hero-title{left:110px;top:318px;font-family:'Titillium Web',sans-serif;font-weight:700;font-size:84px;line-height:92px;color:var(--white)}
.hero-sub{left:110px;top:515px;font-family:'Titillium Web',sans-serif;font-size:20px;color:var(--white)}
.hero-btn{left:110px;top:572px;width:162px;height:64px;background:transparent;border:2px solid var(--white)}

/* welcome */
.portrait{left:113px;top:897px;width:418px;height:430px;border-radius:50%;background:var(--pink)}
.portrait-photo{position:absolute;left:0;top:0;width:418px;height:418px;border-radius:50%;background:radial-gradient(circle at 50% 40%,#7d8196,#3c4257)}
.section-h{font-family:'Titillium Web',sans-serif;font-weight:600;font-size:26px;line-height:34px;color:var(--ink)}
.section-sub{font-size:19px;font-weight:500;color:var(--ink)}
.para{font-size:13.4px;line-height:25.8px;color:var(--text);text-align:justify}
.deco{left:850px;top:1190px;width:350px;height:225px;background:linear-gradient(180deg,rgba(249,217,234,0) 0%,rgba(249,217,234,.5) 100%)}

/* services */
.services{left:0;top:1415px;width:1200px;height:625px;background:linear-gradient(180deg,#EF4E9D,#EC4898)}
.services-title{left:0;top:1475px;width:1200px;text-align:center;font-family:'Titillium Web',sans-serif;font-weight:600;font-size:27px;color:var(--white)}
.services-sub{left:0;top:1548px;width:1200px;text-align:center;font-family:'Titillium Web',sans-serif;font-size:21px;color:var(--white)}
.card{width:210px;text-align:center;color:var(--white)}
.card-photo{width:210px;height:151px;border-radius:14px}
.card-title{margin-top:30px;font-family:'Titillium Web',sans-serif;font-weight:700;font-size:17px;letter-spacing:.3px}
.card-text{margin-top:18px;font-size:13px;line-height:23px;padding:0 4px}
.card.active{background:var(--white);border-radius:16px;padding:8px 8px 20px;width:228px;color:var(--ink)}
.card.active .card-title{color:var(--ink)}
.card-link{margin-top:10px;font-family:'Titillium Web',sans-serif;font-weight:600;font-size:16px;color:var(--pink);display:flex;justify-content:center;align-items:center;gap:6px}

/* specialists */
.frame{border:2px solid var(--pink)}
.spec-photo{left:680px;top:2135px;width:362px;height:412px;background:linear-gradient(160deg,#b4a99a,#9fb6c9 55%,#e6d7cc)}

/* cta */
.cta{left:0;top:2666px;width:1200px;height:300px;background:var(--pink-pale)}
.cta-photo{left:0;top:2666px;width:620px;height:300px;background:linear-gradient(90deg,#dcdcdc 0%,#c8ccd1 55%,rgba(249,217,234,1) 100%)}
.script{font-family:'Great Vibes',cursive;font-size:22px;color:var(--pink)}

/* footer */
.footer{left:0;top:2966px;width:1200px;height:391px;background:var(--black)}
.f-logo{left:120px;top:3085px;font-family:'Titillium Web',sans-serif;font-weight:700;font-size:22px;color:var(--white);display:flex;align-items:center;gap:10px}
.f-logo .logo-dot{background:var(--white)}
.social{top:3195px;width:40px;height:40px;border-radius:50%;background:var(--white)}
.f-head{top:3040px;font-family:'Titillium Web',sans-serif;font-weight:700;font-size:18px;color:var(--white)}
.f-links{left:392px;top:3087px;font-size:15.5px;line-height:26px;color:var(--white)}
.f-row{display:flex;gap:14px;font-size:15.5px;line-height:26px;color:var(--white)}
.news{left:863px;top:3093px;width:226px;height:40px;background:var(--white);border-radius:5px;overflow:hidden}
.news span{position:absolute;left:14px;top:11px;font-size:14px;color:#777}
.news-btn{position:absolute;right:0;top:0;width:54px;height:40px;background:var(--pink);display:flex;align-items:center;justify-content:center}
.copy{left:0;top:3293px;width:1200px;text-align:center;font-size:15.5px;color:var(--white)}
</style>
</head>
<body>

<!-- header -->
<div class="abs topbar"></div>
<div class="abs logo"><span class="logo-dot"></span>Meadowcrest OB/GYN</div>
<div class="abs contact-chip" style="left:375px">
  <span class="chip-icon"><svg width="14" height="14" viewBox="0 0 24 24" fill="#fff"><path d="M6.6 10.8a15.1 15.1 0 0 0 6.6 6.6l2.2-2.2c.3-.3.7-.4 1-.2 1.1.4 2.3.6 3.6.6.6 0 1 .4 1 1V20c0 .6-.4 1-1 1A17 17 0 0 1 3 4c0-.6.4-1 1-1h3.5c.6 0 1 .4 1 1 0 1.3.2 2.5.6 3.6.1.3 0 .7-.2 1z"/></svg></span>(555) 214-0388</div>
<div class="abs contact-chip" style="left:540px">
  <span class="chip-icon"><svg width="14" height="12" viewBox="0 0 24 18" fill="#fff"><path d="M0 0h24L12 9z"/><path d="M0 2l12 9 12-9v16H0z"/></svg></span>hello@meadowcrestwomens.com</div>
<div class="abs search">Search
  <svg style="position:absolute;right:12px;top:10px" width="15" height="15" viewBox="0 0 24 24" fill="none" stroke="#bbb" stroke-width="2.5"><circle cx="10" cy="10" r="7"/><path d="M15 15l6 6"/></svg></div>
<div class="abs nav" style="left:475px">HOME</div>
<div class="abs nav" style="left:567px">SERVICES ▾</div>
<div class="abs nav" style="left:700px">RESOURCES ▾</div>
<div class="abs nav" style="left:858px">ABOUT US</div>
<div class="abs nav" style="left:983px">CONTACT US</div>

<!-- hero -->
<div class="abs hero" role="img" aria-label="Doctor listening with a stethoscope to a smiling pregnant patient in an exam room"></div>
<svg class="abs" style="left:52px;top:470px" width="22" height="38" viewBox="0 0 22 38"><path d="M18 3L4 19l14 16" fill="none" stroke="#fff" stroke-width="4"/></svg>
<svg class="abs" style="left:1122px;top:470px" width="22" height="38" viewBox="0 0 22 38"><path d="M4 3l14 16L4 35" fill="none" stroke="var(--pink)" stroke-width="4"/></svg>
<h1 class="abs hero-title">Meadowcrest<br>OB/GYN</h1>
<p class="abs hero-sub">Personalized Medical Care For Women</p>
<div class="btn hero-btn">Get Started</div>

<!-- welcome -->
<div class="abs deco" role="img" aria-label="Faint line drawing of a doctor and patient"></div>
<div class="abs portrait"><div class="portrait-photo" role="img" aria-label="Portrait of a smiling physician in navy scrubs"></div></div>
<h2 class="abs section-h" style="left:601px;top:893px">Welcome To Meadowcrest Ob/gyn,<br>Brookvale, Ca</h2>
<div class="rule" style="left:601px;top:969px;width:183px"></div>
<p class="abs section-sub" style="left:601px;top:995px">Serving Larkspur Valley Medical Center</p>
<p class="abs para" style="left:601px;top:1037px;width:488px">At Meadowcrest OB/GYN in Brookvale, California, we believe better health starts when the patient is educated. For this reason, we take time to listen to our patients concerns, explain each option available, and to answer any questions our patients may have so that they can make informed decisions. At Meadowcrest OB/GYN, our providers tailor every procedure performed and treatment option recommended to meet the specific needs of our patients. We remain up-to-date on the latest technology and practice guidelines for women’s health.</p>
<div class="btn" style="left:601px;top:1271px;width:157px;height:58px">Learn More</div>

<!-- services -->
<div class="abs services" role="img" aria-label="Soft pink-tinted photo of a doctor with a patient"></div>
<h2 class="abs services-title">How Can We Help You?</h2>
<div class="rule" style="left:509px;top:1525px;width:182px;border-color:var(--pink-pale)"></div>
<p class="abs services-sub">Health Services Offered</p>

<div class="abs card" style="left:120px;top:1626px">
  <div class="card-photo" role="img" aria-label="Hands resting on a pregnant belly" style="background:linear-gradient(135deg,#f4e6dc,#e8c3b2)"></div>
  <div class="card-title">PREGNANCY CARE</div>
  <p class="card-text">Receiving regular care in pregnancy is important for the health of both you and your</p>
</div>
<div class="abs card active" style="left:364px;top:1618px">
  <div class="card-photo" role="img" aria-label="Hand holding a glass of water and a pill pack" style="background:linear-gradient(135deg,#7e9c9a,#d9a996)"></div>
  <div class="card-title">BIRTH CONTROL</div>
  <p class="card-text">Our gynecologists are knowledgeable on all forms of birth control including the IUD,</p>
  <div class="card-link">Learn More <svg width="18" height="10" viewBox="0 0 18 10"><path d="M0 5h16M12 1l4 4-4 4" fill="none" stroke="var(--pink)" stroke-width="1.8"/></svg></div>
</div>
<div class="abs card" style="left:626px;top:1626px">
  <div class="card-photo" role="img" aria-label="Hands holding a red heart beside a stethoscope" style="background:linear-gradient(135deg,#8d8d8d,#c9c9c9)"></div>
  <div class="card-title">WELL WOMAN EXAMS</div>
  <p class="card-text">Our providers will help you to stay healthy by performing a physical exam on you annually.</p>
</div>
<div class="abs card" style="left:879px;top:1626px">
  <div class="card-photo" role="img" aria-label="Woman meditating cross-legged at home" style="background:linear-gradient(135deg,#eef0f2,#b9c6da)"></div>
  <div class="card-title">WOMEN'S HEALTH</div>
  <p class="card-text">Whether you are dealing with painful or irregular periods, fibroids, or other women's</p>
</div>

<!-- specialists -->
<h2 class="abs section-h" style="left:112px;top:2120px">Your Ob/gyn Specialists</h2>
<div class="rule" style="left:112px;top:2170px;width:182px"></div>
<p class="abs section-sub" style="left:112px;top:2195px">Meadowcrest OB/GYN offers</p>
<p class="abs para" style="left:112px;top:2237px;width:487px">Meadowcrest OB/GYN offers you the best care possible in a personalized setting. We are currently accepting patients. Call our office now to make an appointment. Meadowcrest OB/GYN (located near Larkspur Valley Hospital in Brookvale, CA) is a medical office that specializes in Christ-centered healthcare for women of all ages. Our team of exclusively female providers have years of experience taking care of women with a variety of pregnancy and gynecology concerns.Whether you need a routine examination, help during your pregnancy, have questions on birth control, or another female concern, we offer the best care possible for our patients. That is why better health starts here.</p>
<div class="btn" style="left:112px;top:2522px;width:157px;height:58px">Learn More</div>
<div class="abs frame" style="left:672px;top:2127px;width:258px;height:240px;border-right:none;border-bottom:none"></div>
<div class="abs frame" style="left:818px;top:2315px;width:232px;height:240px;border-left:none;border-top:none"></div>
<div class="abs spec-photo" role="img" aria-label="Nurse in blue scrubs holding a newborn baby"></div>

<!-- call to action -->
<div class="abs cta"></div>
<div class="abs cta-photo" role="img" aria-label="Masked doctor reviewing a clipboard with a masked pregnant patient"></div>
<p class="abs script" style="left:620px;width:474px;top:2733px;text-align:center">Better Health Starts Here!</p>
<h2 class="abs heading" style="left:620px;width:474px;top:2770px;text-align:center;font-size:30px;font-weight:400;color:var(--ink)">Now Accepting New Patients</h2>
<div class="btn" style="left:749px;top:2840px;width:216px;height:58px">Book An Appointment</div>

<!-- footer -->
<div class="abs footer"></div>
<div class="abs f-logo"><span class="logo-dot"></span>Meadowcrest OB/GYN</div>
<div class="abs social" style="left:113px" aria-label="Social profile"></div>
<div class="abs social" style="left:168px" aria-label="Social profile"></div>
<div class="abs social" style="left:222px" aria-label="Social profile"></div>
<div class="abs social" style="left:277px" aria-label="Social profile"></div>

<div class="abs f-head" style="left:392px">QUICK LINKS</div>
<div class="abs f-links">Home<br>About Us<br>News<br>Patient Resources<br>Privacy Policy<br>Contact Us</div>

<div class="abs f-head" style="left:584px">CONTACT US</div>
<div class="abs f-row" style="left:586px;top:3093px">
  <svg width="16" height="20" viewBox="0 0 16 20" style="margin-top:4px;flex:none"><path d="M8 0a7 7 0 0 1 7 7c0 5-7 13-7 13S1 12 1 7a7 7 0 0 1 7-7z" fill="#fff"/><circle cx="8" cy="7" r="2.6" fill="#000"/></svg>
  <span>1480 Larkspur Avenue,<br>Suite 210, Brookvale, CA 90000</span></div>
<div class="abs f-row" style="left:586px;top:3161px">
  <svg width="18" height="18" viewBox="0 0 24 24" fill="#fff" style="margin-top:4px;flex:none"><path d="M6.6 10.8a15.1 15.1 0 0 0 6.6 6.6l2.2-2.2c.3-.3.7-.4 1-.2 1.1.4 2.3.6 3.6.6.6 0 1 .4 1 1V20c0 .6-.4 1-1 1A17 17 0 0 1 3 4c0-.6.4-1 1-1h3.5c.6 0 1 .4 1 1 0 1.3.2 2.5.6 3.6.1.3 0 .7-.2 1z"/></svg>
  <span>(555) 214-0388</span></div>
<div class="abs f-row" style="left:586px;top:3195px">
  <svg width="18" height="14" viewBox="0 0 24 18" fill="#fff" style="margin-top:6px;flex:none"><path d="M0 0h24L12 9z"/><path d="M0 2l12 9 12-9v16H0z"/></svg>
  <span>hello@meadowcrestwomens.com</span></div>

<div class="abs f-head" style="left:863px">NEWSLETTER</div>
<div class="abs news"><span>Enter email</span>
  <div class="news-btn"><svg width="16" height="12" viewBox="0 0 24 18" fill="#fff"><path d="M0 0h24L12 9z"/><path d="M0 2l12 9 12-9v16H0z"/></svg></div></div>

<p class="abs copy">©Copyrights 2022 meadowcrestwomens &nbsp; | &nbsp; All Rights Reserved</p>

</body>
</html>
```